Copperleaf Roofing Business Card

This is my current business card. But I’d like to make some changes. Somewhere on the card I’d like to list some of the services we offer. Maybe on the back? But I’d still like to keep the red. White and black modern look.

-residential & commercial roofing
-Roof Repairs & Maintenance
-Storm Damage & Insurance Claims specialist
-Christmas Lights and permanent Christmas lights
Fencing. Windows. Gutters. Siding. Sheetrock, painting.

```html
<!DOCTYPE html>
<html lang="en">
<head>
<meta charset="UTF-8">
<title>Copperleaf Roofing Business Card</title>
<link href="https://fonts.googleapis.com/css2?family=Arimo:wght@400;700&family=Michroma&display=swap" rel="stylesheet">
<style>
  :root {
    --canvas: #e4e5e8;
    --card: #0b0b0c;
    --ink: #ffffff;
    --red: #e3161d;
    --red-deep: #8e0c10;
    --shade: #1c1c1e;
  }
  * { box-sizing: border-box; margin: 0; padding: 0; }
  html, body { width: 1200px; height: 800px; overflow: hidden; }
  body {
    background: var(--canvas);
    display: flex;
    align-items: center;
    justify-content: center;
    gap: 40px;
    font-family: "Arimo", Arial, sans-serif;
  }
  .card {
    position: relative;
    width: 560px;
    height: 320px;
    background: var(--card);
    color: var(--ink);
    overflow: hidden;
    box-shadow: 0 10px 30px rgba(0,0,0,.18);
  }
  .card__mascot-area {
    position: absolute;
    left: 90px; top: -20px;
    width: 240px; height: 230px;
    border-radius: 50%;
    background: radial-gradient(circle, var(--shade) 0%, rgba(28,28,30,0) 70%);
  }
  .card__rule {
    position: absolute;
    left: 28px; right: 60px;
    top: 196px;
    height: 1px;
    background: var(--red-deep);
  }
  .card__band {
    position: absolute;
    left: 0; right: 0; bottom: 0;
    height: 34px;
    background: var(--red-deep);
  }
  .card__band::before {
    content: "";
    position: absolute;
    left: 0; right: 0; top: 0;
    height: 8px;
    background: var(--red);
  }
  .brand {
    position: absolute;
    right: 34px; top: 110px;
    display: flex;
    align-items: center;
    gap: 10px;
  }
  .brand__dot {
    width: 38px; height: 38px;
    border-radius: 50%;
    background: var(--red);
  }
  .brand__name {
    font-weight: 700;
    font-size: 20px;
    line-height: 1.1;
    color: var(--ink);
    text-transform: uppercase;
  }
  .person { position: absolute; left: 30px; top: 34px; }
  .person__name {
    font-family: "Michroma", sans-serif;
    font-size: 22px;
    letter-spacing: 1px;
  }
  .person__role {
    color: var(--red);
    font-size: 12px;
    letter-spacing: 1px;
    margin-top: 4px;
  }
  .contact {
    list-style: none;
    margin-top: 16px;
    font-size: 13.5px;
  }
  .contact li { display: flex; align-items: center; gap: 8px; margin-bottom: 7px; }
  .contact svg { width: 12px; height: 12px; fill: none; stroke: var(--red); stroke-width: 2; }
  .services { position: absolute; left: 30px; top: 30px; }
  .services__title {
    font-family: "Michroma", sans-serif;
    color: var(--red);
    font-size: 17px;
    margin-bottom: 10px;
  }
  .services__list { list-style: none; font-size: 12.5px; line-height: 1.55; }
  .services__list li { position: relative; padding-left: 13px; }
  .services__list li::before {
    content: "";
    position: absolute; left: 0; top: 7px;
    width: 5px; height: 5px; border-radius: 50%;
    background: var(--red);
  }
  .services__list li.plain { padding-left: 0; }
  .services__list li.plain::before { display: none; }
</style>
</head>
<body>
  <section class="card card--front">
    <div class="card__mascot-area" role="img" aria-label="Faint brand mascot decoration"></div>
    <div class="person">
      <h1 class="person__name">DALE MERCER</h1>
      <p class="person__role">OWNER</p>
      <ul class="contact">
        <li><svg viewBox="0 0 12 12"><path d="M3 1 L5 3.5 L4 5 Q5.5 7.5 7 8 L8.5 7 L11 9 L9.5 11 Q3 10 1 2.5 Z"/></svg>682-555-0148</li>
        <li><svg viewBox="0 0 12 12"><rect x="1" y="2.5" width="10" height="7"/><path d="M1 2.5 L6 7 L11 2.5"/></svg>dale@copperleafroofing.co</li>
        <li><svg viewBox="0 0 12 12"><circle cx="6" cy="6" r="5"/><path d="M1 6 H11 M6 1 Q3 6 6 11 Q9 6 6 1"/></svg>www.copperleafroofing.co</li>
      </ul>
    </div>
    <div class="card__rule"></div>
    <div class="brand">
      <span class="brand__dot"></span>
      <span class="brand__name">Copperleaf<br>Roofing</span>
    </div>
    <div class="card__band"></div>
  </section>

  <section class="card card--back">
    <div class="card__mascot-area" role="img" aria-label="Faint brand mascot decoration"></div>
    <div class="services">
      <h2 class="services__title">SERVICES</h2>
      <ul class="services__list">
        <li>Residential &amp; Commercial Roofing</li>
        <li>Roof Repairs &amp; Maintenance</li>
        <li>Storm Damage &amp; Insurance Claims Specialist</li>
        <li>Christmas Lights And Permanent Christmas Lights</li>
        <li class="plain">Fencing. Windows. Gutters. Siding. Sheetrock, painting.</li>
      </ul>
    </div>
    <div class="card__rule"></div>
    <div class="brand">
      <span class="brand__dot"></span>
      <span class="brand__name">Copperleaf<br>Roofing</span>
    </div>
    <div class="card__band"></div>
  </section>
</body>
</html>
```